Marrowby Water Taxi and Transport Business Card

I need business cards for my new water taxi and freight transport business I have started here in Kodiak Alaska. Kodiak is a remote island in the middle of the gulf of Alaska. There are seven native villages around the island and Kodiak is the #2 fishing port in the United States. We also have the largest Coast Guard Base in the U.S. My company will be providing water taxi and freight transport logistics to the villages and many hunting and fishing lodges as well as remote properties around the island.

I would like a business card that isn't status quo, something that stands out, either in feel or appearance. I do like clean minimal designs but it needs to have the necessary contact info on it.

Target Market(s)

remote lodge / property owners, residents of the many villages around Kodiak and any one wanting to enjoy the great outdoors of Kodiak Alaska

Industry/Entity Type

Business

Contact Information for Business Card

I like clean simple designs that aren't cluttered but still provide the necessary information

Colors
0255a3
3277b5
33a4d5
9bcb3c
add136
fbed22
ffc214
f78f20
f37122

Requirements
Must have
• logo and contact info
• Captain Mason Elwick
• www.marrowbyferryline.com
• mason@marrowbyferryline.com

```html
<!DOCTYPE html>
<html lang="en">
<head>
<meta charset="utf-8">
<title>Marrowby Water Taxi and Transport – Business Card</title>
<link href="https://fonts.googleapis.com/css2?family=Montserrat:wght@700&family=Questrial&display=swap" rel="stylesheet">
<style>
  :root {
    --page-bg: #e9ecef;
    --navy-deep: #0b2280;
    --navy: #0255a3;
    --blue-mid: #3277b5;
    --sky: #33a4d5;
    --ice: #dbe9f3;
    --orange: #f37122;
    --orange-soft: #f78f20;
    --white: #ffffff;
    --logo-ink: #12306e;
  }
  html, body {
    margin: 0;
    padding: 0;
    width: 1200px;
    height: 969px;
    overflow: hidden;
    background: var(--page-bg);
  }
  .canvas {
    position: relative;
    width: 1200px;
    height: 969px;
  }
  .business-card {
    position: absolute;
    left: 120px;
    top: 211px;
    width: 960px;
    height: 546px;
    border-radius: 30px;
    overflow: hidden;
    background: linear-gradient(160deg, var(--navy-deep) 0%, var(--navy) 55%, var(--blue-mid) 100%);
    box-shadow: 0 18px 40px rgba(0, 0, 0, 0.18);
    font-family: "Questrial", "Century Gothic", sans-serif;
  }
  .mountain-artwork {
    position: absolute;
    inset: 0;
    background:
      radial-gradient(circle at 86% 24%, var(--orange-soft) 0, var(--orange) 10%, rgba(243,113,34,0) 16%),
      linear-gradient(180deg, rgba(2,85,163,0) 28%, rgba(51,164,213,0.75) 50%, var(--ice) 78%, var(--ice) 100%);
  }
  .contact-block {
    position: absolute;
    left: 36px;
    top: 38px;
    color: var(--white);
  }
  .holder-name {
    margin: 0;
    font-family: "Montserrat", "Century Gothic", sans-serif;
    font-weight: 700;
    font-size: 27px;
    letter-spacing: 0.5px;
    color: var(--orange);
    text-transform: uppercase;
  }
  .holder-role {
    margin: 8px 0 20px;
    font-size: 27px;
  }
  .contact-line {
    margin: 0 0 10px;
    font-size: 22px;
    line-height: 26px;
  }
  .brand-name {
    position: absolute;
    left: 553px;
    top: 398px;
    transform: translateX(-50%);
    text-align: center;
    color: var(--logo-ink);
    font-family: "Questrial", "Century Gothic", sans-serif;
    font-weight: 400;
    white-space: nowrap;
  }
  .brand-main {
    display: block;
    font-size: 48px;
    line-height: 52px;
    letter-spacing: 1px;
  }
  .brand-sub {
    display: block;
    font-size: 21px;
    line-height: 26px;
  }
</style>
</head>
<body>
  <main class="canvas">
    <section class="business-card">
      <div class="mountain-artwork" role="img" aria-label="Illustration of snow-capped blue mountain peaks with an orange sun setting behind them"></div>

      <div class="contact-block">
        <h1 class="holder-name">Mason Elwick</h1>
        <p class="holder-role">Captain</p>
        <p class="contact-line">Phone : 555 014 2290</p>
        <p class="contact-line">mason@marrowbyferryline.com</p>
        <p class="contact-line">marrowbyferryline.com</p>
      </div>

      <div class="brand-name">
        <span class="brand-main">MARROWBY</span>
        <span class="brand-sub">Water Taxi and Transport</span>
      </div>
    </section>
  </main>
</body>
</html>
```